Tech business card design

We need an amazing business card design for our new business 'Pexla' a marketing tech startup based in Sydney, Australia. We provide an online marketplace for businesses to search and buy advertising media, connect with service providers and learn more about marketing. We wish to communicate 'cool tech', reliability and professionalism and design based around our logo.

Target Market(s)

Business Owners

Contact Information for Business Card

Name
Position
Email Address
Website
Phone Number

Font styles to use
Other font styles liked:
• Avenir & Avenir Next

Colors

Designer to choose colors to be used in the design.

```html
<!DOCTYPE html>
<html lang="en">
<head>
<meta charset="utf-8">
<title>Pexla Business Card</title>
<link href="https://fonts.googleapis.com/css2?family=Open+Sans:wght@400;600;700;800&display=swap" rel="stylesheet">
<style>
  :root {
    --backdrop: #e1dedf;
    --card-front: #ffffff;
    --card-back: #414143;
    --navy: #1f2150;
    --ink: #222226;
    --light: #ffffff;
    --edge: #d4d1d2;
  }
  * { margin: 0; padding: 0; box-sizing: border-box; }
  html, body { width: 975px; height: 1200px; overflow: hidden; background: var(--backdrop); }
  body { position: relative; font-family: "Open Sans", sans-serif; color: var(--ink); }

  .card { position: absolute; left: 58px; width: 859px; height: 491px; border-radius: 26px; }
  .card--front { top: 70px; background: var(--card-front); border: 1px solid var(--edge); }
  .card--back { top: 629px; background: var(--card-back); }

  .holder { position: absolute; left: 63px; top: 70px; line-height: 1.25; }
  .holder__name { font-size: 27px; font-weight: 700; color: var(--navy); letter-spacing: 0.2px; }
  .holder__role { font-size: 22px; font-weight: 400; }

  .wordmark { position: absolute; font-weight: 800; letter-spacing: -2px; line-height: 1; }
  .wordmark--front { left: 412px; top: 40px; font-size: 122px; color: var(--navy); }
  .wordmark--back { left: 0; width: 100%; text-align: center; top: 172px; font-size: 140px; color: var(--light); }

  .contacts { position: absolute; left: 66px; top: 200px; list-style: none; }
  .contacts li { display: flex; align-items: center; height: 36px; font-size: 20px; }
  .contacts svg { width: 20px; height: 20px; margin-right: 11px; flex: none; }
  .contacts .web { letter-spacing: 2px; }

  .address { position: absolute; left: 66px; top: 333px; font-size: 21px; line-height: 29px; }

  .back-url { position: absolute; left: 0; width: 100%; text-align: center; top: 399px; font-size: 26px; letter-spacing: 3.5px; color: var(--light); }
</style>
</head>
<body>
  <section class="card card--front">
    <div class="holder">
      <p class="holder__name">JOHN SMITH</p>
      <p class="holder__role">Position</p>
    </div>
    <div class="wordmark wordmark--front">Pexla</div>
    <ul class="contacts">
      <li>
        <svg viewBox="0 0 20 20" aria-hidden="true"><circle cx="10" cy="10" r="9" fill="none" stroke="#222226" stroke-width="1.5"/><path d="M7 5.5l2 2-1 1.2c.6 1.4 1.6 2.4 3 3l1.2-1 2 2-1.3 1.5c-3.3-.3-6.6-3.6-7-7z" fill="#222226"/></svg>
        012-345-6789
      </li>
      <li>
        <svg viewBox="0 0 20 20" aria-hidden="true"><rect x="1" y="4" width="18" height="12" fill="#222226"/><path d="M1.5 4.5L10 11l8.5-6.5M1.5 15.5l6-5M18.5 15.5l-6-5" stroke="#fff" stroke-width="1.3" fill="none"/></svg>
        info@pexla.com
      </li>
      <li class="web">
        <svg viewBox="0 0 20 20" aria-hidden="true" fill="none" stroke="#222226" stroke-width="1.4"><circle cx="10" cy="10" r="8.5"/><ellipse cx="10" cy="10" rx="3.8" ry="8.5"/><path d="M1.5 10h17M3 5.5h14M3 14.5h14"/></svg>
        www.pexla.com
      </li>
    </ul>
    <p class="address">Street name City Name,<br>Zipcode,012345</p>
  </section>

  <section class="card card--back">
    <div class="wordmark wordmark--back">Pexla</div>
    <p class="back-url">www.pexla.com</p>
  </section>
</body>
</html>
```